Luxury travel agency needs a website design

We are a travel agency specializing in booking luxury vacations. We specialize in Hawaii, Europe and Caribbean, but will do all vacations. I want a very classy website design which would attract luxury clients. The company name is "Harbors and Hammocks Travel Agency". Would love the web design to go with the color scheme of the logo. Hex codes included in files. Logo is attached. Would also love more Grey in the website. I want it very elegant

Coding

Coded - Design and coding required

Font styles to use
Sans Serif
Decorative

Requirements
Must have
• - Consultation Tab or a page where the client can fill out a short form about what vacation that they would want to book. I want this info to be sent to me in order for me to contact them.
- Somewhere with my contact info "email: marla@harborsandhammockstravel.example and phone number"
- Social media links
- About section "Marla Dunbevy - Agency Owner (picture provided)
Marla has been traveling full time for the passed two years and has been very passionate about travel from a young age. Marla is dedicated to working closely with clients to book their dream vacation.
Marla's specializations include honeymoons and anniversaries focusing on travel in Europe, Hawaii and all inclusive resorts in the Caribbean.

```html
<!DOCTYPE html>
<html lang="en">
<head>
<meta charset="utf-8">
<title>Harbors and Hammocks Travel Agency – Specialization</title>
<link href="https://fonts.googleapis.com/css2?family=Montserrat:wght@400;500;600;700&family=Kaushan+Script&family=Cinzel+Decorative:wght@700&display=swap" rel="stylesheet">
<style>
  :root{
    --orange:#f0894a;
    --orange-deep:#e8733a;
    --gold:#f4b24f;
    --ink:#2b2b2b;
    --grey:#5e5e5e;
    --grey-light:#e6e6e6;
    --footer:#0c0c0c;
    --white:#ffffff;
    --sand:#d8c39a;
  }
  *{box-sizing:border-box;margin:0;padding:0}
  html,body{width:1200px;height:3400px;overflow:hidden;background:var(--white)}
  body{position:relative;font-family:"Montserrat",sans-serif;color:var(--ink)}

  .top-bar{position:absolute;left:0;top:0;width:1200px;height:24px;background:var(--orange);
    display:flex;align-items:center;justify-content:space-between;padding:0 170px 0 180px;color:var(--white);font-size:11px}
  .top-bar .contact-email{display:flex;align-items:center;gap:6px}
  .top-bar .right{display:flex;align-items:center;gap:14px}
  .social{display:flex;gap:6px}
  .social span{width:12px;height:12px;border-radius:50%;background:var(--white);display:block}

  .hero{position:absolute;left:0;top:24px;width:1200px;height:600px;overflow:hidden}
  .hero-photo{position:absolute;inset:0;
    background:linear-gradient(180deg,#c9b7b9 0%,#e7c6a8 28%,#f3c98f 42%,#9fb4c2 52%,#5d8298 70%,#2f4d5c 100%)}
  .hero-curve{position:absolute;left:0;bottom:0}
  .brand{position:absolute;left:180px;top:50px;color:var(--white);font-family:"Montserrat",sans-serif;font-weight:700;font-size:28px;line-height:1.1;display:flex;align-items:center;gap:12px}
  .brand .mark{width:34px;height:34px;border-radius:50%;background:var(--white)}
  .nav{position:absolute;left:550px;top:96px;display:flex;align-items:center;gap:34px;color:var(--white);font-size:13px;font-weight:600;letter-spacing:.5px}
  .nav .consult{background:#3d3d3d;padding:10px 16px;border-radius:3px}
  .hero-title{position:absolute;left:680px;top:256px;font-family:"Cinzel Decorative",serif;font-size:40px;font-weight:700;color:var(--white);letter-spacing:1px;white-space:nowrap}

  .section-title{position:absolute;left:0;top:658px;width:1200px;text-align:center;font-family:"Kaushan Script",cursive;font-size:46px}
  .section-title .name{color:var(--ink)}
  .section-title .accent{background:linear-gradient(90deg,var(--orange-deep),var(--gold));-webkit-background-clip:text;background-clip:text;color:transparent}

  .card{position:absolute;left:180px;width:840px;height:265px;background:var(--white);border:1px solid var(--grey-light);
    border-radius:14px;box-shadow:0 10px 24px rgba(0,0,0,.12);display:flex;align-items:center;padding:0 28px 0 20px;gap:30px}
  .card-photo{flex:0 0 250px;height:205px;border-radius:10px}
  .card h3{font-size:22px;font-weight:500;color:var(--ink);margin-bottom:14px;letter-spacing:.5px}
  .card p{font-size:12.5px;line-height:1.75;color:var(--grey)}

  .p-hawaii{background:linear-gradient(180deg,#9cc7e3 0%,#5fa2c6 45%,#3f7f4a 70%,#d9c79c 100%)}
  .p-caribbean{background:linear-gradient(180deg,#a9d3ef 0%,#6ab1d8 35%,#3e9a8f 60%,#3b7a3f 100%)}
  .p-mexico{background:linear-gradient(180deg,#5d8ed0 0%,#9bb7de 40%,#c98f5b 65%,#7a4a2e 100%)}
  .p-europe{background:linear-gradient(180deg,#2d4d8a 0%,#6d7fb8 40%,#d6a06a 70%,#5b4a52 100%)}
  .p-parks{background:linear-gradient(180deg,#4c90d6 0%,#8ec0ea 40%,#3f7d46 70%,#b3885c 100%)}

  .footer-photo{position:absolute;left:0;top:2440px;width:1200px;height:480px;
    background:linear-gradient(180deg,#1f3c55 0%,#e79a5a 28%,#f3c27a 40%,#6e8ea2 58%,#2e5a4a 78%,#1a2f2a 100%)}
  .footer-wave{position:absolute;left:0;top:2440px}
  .footer-brand{position:absolute;left:0;top:2650px;width:1200px;text-align:center;color:var(--white);font-weight:700;font-size:52px;letter-spacing:1px}
  .footer-brand small{display:block;font-size:18px;font-weight:700;letter-spacing:8px;margin-top:6px}

  .footer{position:absolute;left:0;top:2920px;width:1200px;height:480px;background:var(--footer);color:var(--white)}
  .footer-logo{position:absolute;left:180px;top:120px;font-weight:700;font-size:30px;line-height:1.15;display:flex;align-items:center;gap:12px}
  .footer-logo .mark{width:34px;height:34px;border-radius:50%;background:var(--white)}
  .links{position:absolute;left:570px;top:54px}
  .footer h4{font-size:14px;font-weight:600;letter-spacing:1px;margin-bottom:18px}
  .links li{list-style:none;font-size:12.5px;line-height:2}
  .newsletter{position:absolute;left:780px;top:54px;width:260px}
  .newsletter p{font-size:12.5px;line-height:1.6;color:#d0d0d0;margin-bottom:24px}
  .field{width:245px;height:38px;border-radius:19px;background:var(--white);color:#777;font-size:12px;padding:11px 18px;margin-bottom:18px}
  .subscribe{display:inline-block;background:var(--orange);border-radius:18px;padding:10px 22px;font-size:12px;font-weight:600}
  .rule{position:absolute;left:180px;top:360px;width:840px;height:1px;background:#3a3a3a}
  .copyright{position:absolute;left:0;top:412px;width:1200px;text-align:center;font-size:12px;color:#d0d0d0}
  .edge-badge{position:absolute;left:-40px;top:142px;width:80px;height:80px;border-radius:50%;background:var(--sand)}
</style>
</head>
<body>

<header class="top-bar">
  <div class="contact-email">
    <svg width="12" height="10" viewBox="0 0 12 10"><rect x="0.5" y="0.5" width="11" height="9" fill="none" stroke="#fff"/><path d="M0.5 0.5 L6 5 L11.5 0.5" fill="none" stroke="#fff"/></svg>
    marla@harborsandhammockstravel.example
  </div>
  <div class="right">
    <span>
      <svg width="10" height="10" viewBox="0 0 10 10"><path d="M2 0.5 L3.8 0.5 L4.5 3 L3.2 4 Q4.5 6 6 6.8 L7 5.5 L9.5 6.2 L9.5 8 Q9.5 9.5 8 9.5 Q0.5 8.5 0.5 2 Q0.5 0.5 2 0.5Z" fill="#fff"/></svg>
      (480) 555-0142
    </span>
    <div class="social"><span></span><span></span><span></span><span></span><span></span></div>
  </div>
</header>

<section class="hero">
  <div class="hero-photo" role="img" aria-label="Sunset over a tropical bay with rocks and palm fronds"></div>
  <div class="brand"><span class="mark"></span>Harbors &amp; Hammocks</div>
  <nav class="nav">
    <span>HOME</span><span>ABOUT</span><span>CONTACT</span><span class="consult">SCHEDULE A CONSULT</span>
  </nav>
  <h1 class="hero-title">Specialization</h1>
  <svg class="hero-curve" width="1200" height="120" viewBox="0 0 1200 120"><path d="M0 40 Q600 150 1200 40 L1200 120 L0 120Z" fill="#fff"/></svg>
</section>

<h2 class="section-title"><span class="name">Marla's</span> <span class="accent">Specializations</span></h2>

<article class="card" style="top:790px">
  <div class="card-photo p-hawaii" role="img" aria-label="Hawaiian beach with green cliffs"></div>
  <div>
    <h3>HAWAII</h3>
    <p>Hawaii is one of the most beloved states, set in the Pacific Ocean and made up of several islands. Each island has its own charm, from calm beaches to volcanic trails. Whether you seek relaxing resorts, cultural experiences or outdoor adventure, we will match you with the island that fits your dream escape.</p>
  </div>
</article>

<article class="card" style="top:1108px">
  <div class="card-photo p-caribbean" role="img" aria-label="Caribbean island coastline seen from above"></div>
  <div>
    <h3>THE CARIBBEAN ISLANDS</h3>
    <p>These are a chain of islands located in the Caribbean Sea. Each island and country is very unique, but most of them are tropical in nature. These islands are very popular for beach goers and anyone looking for an all-inclusive resort. We can match you with your preferred destination and plan the perfect stay.</p>
  </div>
</article>

<article class="card" style="top:1428px">
  <div class="card-photo p-mexico" role="img" aria-label="Colonial church towers in a Mexican town"></div>
  <div>
    <h3>MEXICO</h3>
    <p>Located in North America, Mexico is a very diverse country to visit. Popular locations include the coast, ancient ruins and colorful colonial towns. Whether you want to relax on a sunny beach or explore lively markets, Mexico is your destination. Immerse yourself in the culture while staying on beautiful shores.</p>
  </div>
</article>

<article class="card" style="top:1750px">
  <div class="card-photo p-europe" role="img" aria-label="European city square at dusk"></div>
  <div>
    <h3>EUROPE</h3>
    <p>Europe is a very large and diverse continent, popular for its culture and history. Whether you want to visit the beautiful coasts of Italy and Greece, immerse yourself in historic cities, or take a river cruise through castles and vineyards, we can build your perfect vacation with a local guide to show you the way.</p>
  </div>
</article>

<article class="card" style="top:2068px">
  <div class="card-photo p-parks" role="img" aria-label="Theme park avenue lined with palm trees"></div>
  <div>
    <h3>CASTLEBROOK AND STARLIGHT STUDIOS</h3>
    <p>Castlebrook and Starlight Studios are very popular theme parks for families to visit. Visiting theme parks can be very overwhelming, especially with families. We are in the know about all things at both resorts and will sort out the tickets, hotels and schedules so you can focus on making memories.</p>
  </div>
</article>

<div class="footer-photo" role="img" aria-label="Aerial view of a tropical island coast at sunset"></div>
<svg class="footer-wave" width="1200" height="70" viewBox="0 0 1200 70"><path d="M0 0 L1200 0 L1200 20 Q600 70 0 20Z" fill="#fff"/></svg>
<div class="footer-brand">Harbors &amp; Hammocks<small>TRAVEL AGENCY</small></div>

<footer class="footer">
  <div class="edge-badge"></div>
  <div class="footer-logo"><span class="mark"></span>Harbors &amp;<br>Hammocks</div>
  <div class="links">
    <h4>QUICK LINKS</h4>
    <ul><li>Home</li><li>About Us</li><li>Blog</li><li>Destinations</li><li>Travel</li><li>Contact Us</li></ul>
  </div>
  <div class="newsletter">
    <h4>SUBSCRIBE TO OUR<br>NEWSLETTER</h4>
    <p>Get travel tips and exclusive offers in your inbox.</p>
    <div class="field">Email</div>
    <span class="subscribe">SUBSCRIBE</span>
  </div>
  <div class="rule"></div>
  <div class="copyright">Copyright © 2021 Harbors and Hammocks. All Rights Reserved.</div>
</footer>

</body>
</html>
```